Refresh and update our Juice bottle label to a more vibrant and eye catching brand

We’ve had this label and included trademarked logo for the past 10 years. We do change the name of the juice ands its ingredients accordingly.
I want to up-date this round juice bottle label so it is more eye catching , trendy and clearly screams (healthy/juice/delicious/refreshing/beauty/youthful/high energy.
I have attached my trademarked logos as well as examples of a few labels. I also attached a few pictures of our juices with the current label which is a 2x4 inch front and back. I want you to see how colorful our juice is. I want the updated label to include out trademarked logo somehow but add in some color or graphics that speak to the message above in (). Open to adding color and even having a wrap around label instead of front and back=

Target Market(s)

Upscale women:men, age 20-65 40:30 ratio, health/ fitness/ body aware, anti aging/ high energy/ prevention of disease. Clientele is primarily caucasian.

Industry/Entity Type

Beverage, cold-pressed juice, wellness

Font styles to use
Sans Serif

Colors
59FF00
82FF00
B8FF75
E3FFCB
F4FFEA
EB3D1F
EC4F4E
F09395
F8D3D4
FCEDEE
E54698
E96AAD
F1A4CE
F9D9EA
FCEFF6
6B429C
8869AF
B7A5CE
E3DAEB
F3F0F8

Requirements
Must have
• My trademarked logo incorporated somehow. Bright/simple/modern/trendy style. I need to be able to change out the name of the juice and its ingredients and nutritional information. I want the label to say “100% Juice” basically this all needs to be on it: Name and Address. The name and address of your juicing business. ... Name of the Food. You should list the name of the food that is commonly used. ... What is the Amount of Juice inside of the bottle? ... % of juice declaration. ... Ingredients. ... Food Allergen (made in a facility with nuts). ... The Disclaimer. Must say “cold-pressed juice”
Nice to have
• Maybe a graphic image of a piece of fruit like a lemon with sliced cucumbers, I want vibrant colors added such as maybe use hot pink -outline or graphic on my Try Sun Orchard? since the juice is pink. Or a bright yellow on my Try Kelp Rally? Or a bright green on Mira Dew. Maybe some wording like “no added sugar or preservatives”, “gluten free”
Should not have
• No health guarantees

```html
<!DOCTYPE html>
<html lang="en">
<head>
<meta charset="utf-8">
<title>Try Kelp Rally? – Juice Label</title>
<link rel="stylesheet" href="https://fonts.googleapis.com/css2?family=Bebas+Neue&family=Lato:wght@400;700&display=swap">
<style>
  :root {
    --backdrop: #c69834;
    --label-white: #ffffff;
    --sun-yellow: #e8bd00;
    --band-yellow: #eabf00;
    --text-yellow: #e6b800;
    --brand-green: #1f7a34;
    --fruit-light: #ffe36a;
    --fruit-deep: #f0b400;
  }
  html, body {
    margin: 0;
    padding: 0;
    width: 1200px;
    height: 848px;
    overflow: hidden;
    background: var(--backdrop);
  }
  .canvas {
    position: relative;
    width: 1200px;
    height: 848px;
    background: var(--backdrop);
  }
  .label {
    position: absolute;
    top: 128px;
    width: 296px;
    height: 591px;
    background: var(--label-white);
    box-shadow: 0 4px 10px rgba(0, 0, 0, 0.18);
    overflow: hidden;
  }
  .label--back { left: 278px; }
  .label--front { left: 626px; }

  .brand-mark {
    position: absolute;
    display: flex;
    align-items: center;
    gap: 8px;
    font-family: "Bebas Neue", sans-serif;
    color: var(--brand-green);
    white-space: nowrap;
  }
  .brand-mark__dot {
    display: block;
    border-radius: 50%;
    background: var(--brand-green);
  }

  /* Back label */
  .label--back .brand-mark {
    top: 38px;
    left: 0;
    width: 100%;
    justify-content: center;
    font-size: 38px;
    line-height: 1;
  }
  .label--back .brand-mark__dot { width: 22px; height: 22px; }

  .back-copy {
    position: absolute;
    left: 18px;
    right: 18px;
    text-align: center;
    color: var(--text-yellow);
    margin: 0;
  }
  .back-copy--shelf-life {
    top: 141px;
    font-family: "Bebas Neue", sans-serif;
    font-size: 22px;
    line-height: 25px;
    letter-spacing: 0.3px;
  }
  .back-copy--facts {
    top: 230px;
    font-family: "Lato", sans-serif;
    font-size: 11.2px;
    line-height: 15px;
  }
  .back-copy--warning {
    top: 298px;
    font-family: "Lato", sans-serif;
    font-size: 11.2px;
    line-height: 14.7px;
  }
  .back-copy--warning strong { font-weight: 400; font-size: 12.5px; }
  .back-copy--address {
    top: 378px;
    font-family: "Lato", sans-serif;
    font-size: 11.2px;
  }
  .back-copy--volume {
    top: 432px;
    font-family: "Lato", sans-serif;
    font-size: 11.2px;
  }
  .back-copy--web {
    top: 503px;
    font-family: "Bebas Neue", sans-serif;
    font-size: 18px;
    letter-spacing: 0.4px;
  }

  /* Front label */
  .name-band {
    position: absolute;
    left: 0;
    top: 0;
    width: 118px;
    height: 100%;
    background: var(--band-yellow);
  }
  .label--front .brand-mark {
    top: 62px;
    left: 40px;
    font-size: 36px;
    line-height: 1;
  }
  .label--front .brand-mark__dot { width: 22px; height: 22px; }

  .juice-name {
    position: absolute;
    left: 60px;
    bottom: 30px;
    margin: 0;
    transform: rotate(-90deg);
    transform-origin: 0 0;
    translate: -33px 0;
    font-family: "Bebas Neue", sans-serif;
    font-weight: 400;
    font-size: 72px;
    line-height: 66px;
    color: var(--label-white);
    white-space: nowrap;
    letter-spacing: 0.5px;
  }

  .ingredients {
    position: absolute;
    left: 122px;
    top: 158px;
    margin: 0;
    padding: 0;
    list-style: none;
    font-family: "Bebas Neue", sans-serif;
    font-size: 31px;
    line-height: 44.5px;
    color: var(--text-yellow);
  }

  .fruit-art {
    position: absolute;
    left: 120px;
    top: 353px;
    width: 170px;
    height: 222px;
  }
</style>
</head>
<body>
<main class="canvas">

  <section class="label label--back" aria-label="Back label">
    <div class="brand-mark"><span class="brand-mark__dot"></span>Leafline Juicery</div>
    <p class="back-copy back-copy--shelf-life">Best if used within 5 days of<br>purchase</p>
    <p class="back-copy back-copy--facts">100% VEGETABLE &amp; FRUIT JUICE Perishable Keep Refrigerated&nbsp; Shake Well *separation is natural*</p>
    <p class="back-copy back-copy--warning"><strong>WARNING</strong>: This product has not been pasteurized and, therefore may contain harmful bacteria that can cause serious illness in children, the elderly, and persons with weakened immune systems.</p>
    <p class="back-copy back-copy--address">1480 Marlow Ave #7, Seabrook, CA 92610</p>
    <p class="back-copy back-copy--volume">Net Wt. 12oz (354mL)</p>
    <p class="back-copy back-copy--web">LEAFLINEJUICERY.COM</p>
  </section>

  <section class="label label--front" aria-label="Front label">
    <div class="name-band"></div>
    <div class="brand-mark"><span class="brand-mark__dot"></span>Leafline Juicery</div>
    <h1 class="juice-name">Try Kelp Rally?</h1>
    <ul class="ingredients">
      <li>Pineapple</li>
      <li>Fuji Apple</li>
      <li>Lemon</li>
      <li>Turmeric Root</li>
    </ul>
    <svg class="fruit-art" viewBox="0 0 170 222" role="img" aria-label="Illustration of a sliced yellow fruit with a green leaf and a juice splash">
      <defs>
        <radialGradient id="fruitGlow" cx="50%" cy="55%" r="55%">
          <stop offset="0%" stop-color="var(--fruit-light)"/>
          <stop offset="70%" stop-color="var(--fruit-deep)"/>
          <stop offset="100%" stop-color="#ffffff" stop-opacity="0"/>
        </radialGradient>
      </defs>
      <rect width="170" height="222" fill="url(#fruitGlow)"/>
    </svg>
  </section>

</main>
</body>
</html>
```